Indonesian B2B Company (Bawo Materia) - Stationery Design

Bawo Materia needs a corporate, bold and professional-looking stationery design.

Bawo Materia is a new Indonesian company manufacturing, marketing and distributing various ingredients / raw materials such as flavours, fragrance, colours, sweeteners, preservatives for the food & beverage, pharmaceutical, personal care and other household goods industries.

It is a business to business (B2B) company as we supply various natural and synthetic raw materials to various consumer goods manufacturers. We therefore need a logo/identity with corporate and industrial style.

Bawo Materia is a startup company which belongs to a larger Tunas Mekar group of companies (http://tunasmekar.examplebiz.net/about) that focuses in the mining, petroleum and energy businesses. Bawo Materia would like to focus in providing good quality, safe, reliable and affordable ingredients for the industries. Our tagline is "Quality Inputs for Growth"
Updates

We have updated some information including our requirements and contact details to be shown in the stationery. Please check the project brief.

Regards,

Bawo Materia

Target Market(s)

Manufacturers of food & beverages, personal care, pharmaceutical and other FMCG factories.

Industry/Entity Type

Business

Requirements
Must have
• Smart, professional and corporate touches in the stationery designs. We require designs for:
1. Letterhead
2. Envelope (with and without window)
3. Name card
4. Powerpoint presentation template
5. CD label
6. Small memo / with compliments card

Contact details:

Company name:
PT Bawo Ingredients

Address:
Ruko Puri Lestari Selatan, Blok F07 no: 11-12
Sunter Jaya Utara, 14350
Indonesia

Tel:+62 21 638 2097
Fax:+62 21 638 2096
Email: info@bawo-ingredients.co.id
Website: www.bawo-ingredients.co.id

```html
<!DOCTYPE html>
<html lang="en">
<head>
<meta charset="utf-8">
<title>Bawo Materia – Presentation Template</title>
<link rel="stylesheet" href="https://fonts.googleapis.com/css2?family=Roboto+Condensed:wght@700&family=Roboto:wght@400;700&display=swap">
<style>
  :root {
    --backdrop: #e4e2df;
    --slide-bg: #ffffff;
    --brand-red: #c4161c;
    --brand-red-deep: #8e0a12;
    --brand-crimson: #d8232a;
    --brand-orange: #f7a43b;
    --ink-grey: #555555;
    --rule-grey: #9a9a9a;
    --divider: #e3c9c9;
  }
  * { box-sizing: border-box; margin: 0; padding: 0; }
  html, body { width: 1200px; height: 900px; overflow: hidden; }
  body {
    background: var(--backdrop);
    position: relative;
    font-family: "Roboto", Arial, sans-serif;
  }
  .slide {
    position: absolute;
    top: 250px;
    width: 537px;
    height: 404px;
    background: var(--slide-bg);
    overflow: hidden;
    box-shadow: 0 2px 6px rgba(0,0,0,0.18);
  }
  .slide--title { left: 63px; }
  .slide--content { left: 623px; }

  .wave-band {
    position: absolute;
    left: 0; bottom: 0;
    width: 537px; height: 104px;
    display: block;
  }

  /* Title slide */
  .brand-block {
    position: absolute;
    left: 40px; top: 92px;
    width: 140px;
    text-align: center;
  }
  .brand-mark {
    display: block;
    width: 34px; height: 34px;
    margin: 0 auto 14px;
    background: var(--brand-red);
  }
  .brand-name {
    font-family: "Roboto Condensed", "Arial Narrow", sans-serif;
    font-weight: 700;
    font-size: 16px;
    color: var(--brand-red);
    white-space: nowrap;
  }
  .brand-tagline {
    font-size: 7.5px;
    color: var(--ink-grey);
    margin-top: 2px;
    white-space: nowrap;
  }
  .title-divider {
    position: absolute;
    left: 189px; top: 50px;
    width: 1px; height: 180px;
    background: var(--divider);
  }
  .title-text {
    position: absolute;
    left: 209px; top: 103px;
  }
  .title-text__heading {
    font-family: "Roboto Condensed", "Arial Narrow", sans-serif;
    font-weight: 700;
    font-size: 41px;
    line-height: 46px;
    color: var(--brand-red);
    letter-spacing: 0.3px;
  }
  .title-text__subheading {
    font-size: 17px;
    color: var(--ink-grey);
    margin-top: 2px;
  }

  /* Content slide */
  .content-header {
    position: absolute;
    left: 0; top: 0;
    width: 100%; height: 54px;
    border-bottom: 1.5px solid var(--rule-grey);
  }
  .content-header__title {
    position: absolute;
    left: 26px; top: 18px;
    font-family: "Roboto Condensed", "Arial Narrow", sans-serif;
    font-weight: 700;
    font-size: 19px;
    color: var(--brand-red);
  }
  .content-header__brand {
    position: absolute;
    right: 16px; top: 16px;
    display: flex;
    align-items: center;
    gap: 6px;
  }
  .content-header__mark {
    width: 14px; height: 14px;
    background: var(--brand-red);
  }
  .content-header__name {
    font-family: "Roboto Condensed", "Arial Narrow", sans-serif;
    font-weight: 700;
    font-size: 12px;
    color: var(--brand-red);
  }
</style>
</head>
<body>

<section class="slide slide--title">
  <div class="brand-block">
    <span class="brand-mark"></span>
    <div class="brand-name">Bawo Materia</div>
    <div class="brand-tagline">Quality Inputs for Growth</div>
  </div>
  <div class="title-divider"></div>
  <div class="title-text">
    <h1 class="title-text__heading">LOREM IPSUM<br>DOLOR SIT AMET</h1>
    <p class="title-text__subheading">Lorem Ipsum Dolor sit Amet</p>
  </div>
  <svg class="wave-band" viewBox="0 0 537 104" preserveAspectRatio="none" aria-hidden="true">
    <defs>
      <linearGradient id="redSweepA" x1="0" x2="1" y1="0" y2="0">
        <stop offset="0" stop-color="#c4161c"/>
        <stop offset="0.6" stop-color="#9e0d15"/>
        <stop offset="1" stop-color="#b3141b"/>
      </linearGradient>
    </defs>
    <path d="M0,12 C150,22 330,34 537,46 L537,104 L0,104 Z" fill="url(#redSweepA)"/>
    <path d="M0,44 C180,50 380,52 537,40 L537,58 C380,68 190,66 0,62 Z" fill="#7a0810"/>
    <path d="M150,104 C300,80 430,40 537,2 L537,18 C440,52 330,86 250,104 Z" fill="#f7a43b"/>
    <path d="M0,76 C200,70 380,76 537,62 L537,104 L0,104 Z" fill="#d8232a"/>
    <path d="M0,76 C200,70 380,76 537,62" fill="none" stroke="#ffffff" stroke-opacity="0.5" stroke-width="1"/>
  </svg>
</section>

<section class="slide slide--content">
  <header class="content-header">
    <h2 class="content-header__title">LOREM IPSUM DOLOR SIT AMET</h2>
    <div class="content-header__brand">
      <span class="content-header__mark"></span>
      <span class="content-header__name">Bawo Materia</span>
    </div>
  </header>
  <svg class="wave-band" viewBox="0 0 537 104" preserveAspectRatio="none" aria-hidden="true">
    <defs>
      <linearGradient id="redSweepB" x1="0" x2="1" y1="0" y2="0">
        <stop offset="0" stop-color="#c4161c"/>
        <stop offset="0.6" stop-color="#9e0d15"/>
        <stop offset="1" stop-color="#b3141b"/>
      </linearGradient>
    </defs>
    <path d="M0,12 C150,22 330,34 537,46 L537,104 L0,104 Z" fill="url(#redSweepB)"/>
    <path d="M0,44 C180,50 380,52 537,40 L537,58 C380,68 190,66 0,62 Z" fill="#7a0810"/>
    <path d="M150,104 C300,80 430,40 537,2 L537,18 C440,52 330,86 250,104 Z" fill="#f7a43b"/>
    <path d="M0,76 C200,70 380,76 537,62 L537,104 L0,104 Z" fill="#d8232a"/>
    <path d="M0,76 C200,70 380,76 537,62" fill="none" stroke="#ffffff" stroke-opacity="0.5" stroke-width="1"/>
  </svg>
</section>

</body>
</html>
```